UI/ UX Design for ERP Software

We need a new UX/UI interface for a ERP software for property managers. Our CMMS / ERP solution is made based on responsive design technologies and is coded in PHP.
The overall UX to be similar to Tev Ulna - easy navigation, intuitive menus.

Industry/Entity Type

Property Management

Number of Pages Required

5+ page

Requirements
Must have
• Round dock buttons
Consistent icons across the application
Enough Spacing between buttons/icons/ menu
Consistent Font
Nice to have
• We would like the UX to allow the users to use the application without /minimum training.
Should not have
• we don't want anything that is classic with respect to UX

```html
<!DOCTYPE html>
<html lang="en">
<head>
<meta charset="utf-8">
<title>Active Dashboard</title>
<link rel="stylesheet" href="https://fonts.googleapis.com/css2?family=Roboto:wght@400;500&display=swap">
<style>
:root{
  --page:#eaf3fb;
  --header:#0620a0;
  --side-top:#1638c8;
  --side-bottom:#2a3fcf;
  --side-active:#0a22a8;
  --orange:#e8904c;
  --green:#38c02a;
  --pink:#f0416f;
  --blue-card:#1f5fc0;
  --cyan:#00bff6;
  --royal:#2b36c8;
  --purple:#45309a;
  --panel:#f5f9fd;
  --col-pink:#f5e5ec;
  --col-blue:#c5dff8;
  --bar:#77b4f0;
  --grid:#8d8d8d;
  --legend:#02a8e4;
  --white:#ffffff;
  --ink:#333333;
}
*{box-sizing:border-box;margin:0;padding:0}
html,body{width:1200px;height:643px;overflow:hidden}
body{position:relative;background:var(--page);font-family:"Roboto",Arial,sans-serif;color:var(--white)}
.topbar{position:absolute;left:0;top:0;width:1030px;height:53px;background:var(--header);display:flex;align-items:center;padding-left:31px;gap:12px;font-size:14.5px}
.sidebar{position:absolute;left:1030px;top:0;width:170px;height:643px;background:linear-gradient(180deg,var(--side-top),var(--side-bottom));border-radius:10px 0 0 10px;padding-top:5px}
.nav-item{display:flex;align-items:center;height:28.7px;padding-left:12px;font-size:10.5px;gap:0}
.nav-item svg{width:15px;height:15px;flex:none;margin-right:21px}
.nav-item.active{background:var(--side-active);border-radius:8px;margin-right:17px}
.pill{position:absolute;left:26px;width:163px;border-radius:15px;display:flex;align-items:center;justify-content:center;gap:7px;font-size:10.5px}
.range{top:76px;height:31px;background:var(--orange);left:25px}
.dates{top:118px;height:39px;background:var(--green);border-radius:20px;font-size:10px}
.stat{position:absolute;border-radius:14px;display:flex;flex-direction:column;align-items:center;justify-content:center;text-align:center}
.stat .value{font-size:14px;margin-bottom:6px}
.stat .label{display:flex;align-items:center;gap:6px;font-size:10.5px}
.stat.small .label{font-size:10px}
.stat.area .value{font-size:15.5px;margin-bottom:9px}
.stat.area .label{font-size:10.5px}
.props{left:25px;top:167px;width:77px;height:63px;background:var(--pink)}
.tenants{left:112px;top:167px;width:78px;height:63px;background:var(--blue-card)}
.total{left:25px;top:241px;width:165px;height:91px;background:var(--cyan)}
.rented{left:24px;top:343px;width:165px;height:91px;background:var(--royal)}
.vacant{left:25px;top:446px;width:165px;height:91px;background:var(--purple)}
.chart-panel{position:absolute;left:213px;top:77px;width:793px;height:460px;background:var(--panel);border-radius:16px}
.chart-panel svg{position:absolute;left:0;top:0}
.legend{position:absolute;left:25px;top:554px;width:981px;height:71px;background:var(--legend);border-radius:18px;font-size:10.5px}
.legend-item{position:absolute;display:flex;align-items:center;gap:8px}
.dot{width:15px;height:15px;border-radius:50%;border:1px solid rgba(255,255,255,.8)}
</style>
</head>
<body>

<header class="topbar">
  <svg width="20" height="18" viewBox="0 0 20 18" aria-hidden="true"><path d="M10 0 L20 9 H17 V18 H12 V12 H8 V18 H3 V9 H0 Z" fill="#fff"/></svg>
  <span>Active Dashboard</span>
</header>

<div class="pill range">
  <svg width="12" height="12" viewBox="0 0 12 12" aria-hidden="true"><circle cx="6" cy="6" r="5.5" fill="#fff"/><path d="M6 3 V6 H8.5" stroke="#e8904c" stroke-width="1.3" fill="none"/></svg>
  Last 7 Days
  <svg width="10" height="8" viewBox="0 0 10 8" aria-hidden="true"><path d="M0 0 H10 L5 8 Z" fill="#fff"/></svg>
</div>
<div class="pill dates">
  <svg width="13" height="12" viewBox="0 0 13 12" aria-hidden="true"><rect x="0" y="1" width="13" height="11" rx="1" fill="#fff"/><rect x="1.5" y="4" width="10" height="6.5" fill="#38c02a"/><rect x="3" y="5.5" width="2" height="1.5" fill="#fff"/><rect x="6" y="5.5" width="2" height="1.5" fill="#fff"/><rect x="9" y="5.5" width="1.5" height="1.5" fill="#fff"/><rect x="3" y="8" width="2" height="1.5" fill="#fff"/><rect x="6" y="8" width="2" height="1.5" fill="#fff"/></svg>
  27/12/2020 - 03/01/2021
  <svg width="10" height="8" viewBox="0 0 10 8" aria-hidden="true"><path d="M0 0 H10 L5 8 Z" fill="#fff"/></svg>
</div>

<div class="stat small props">
  <div class="value">3</div>
  <div class="label"><svg width="12" height="12" viewBox="0 0 12 12" aria-hidden="true"><circle cx="6" cy="6" r="6" fill="#fff"/><path d="M6 2.5 a2.3 2.3 0 0 1 2.3 2.3 C8.3 6.5 6 9 6 9 S3.7 6.5 3.7 4.8 A2.3 2.3 0 0 1 6 2.5Z" fill="#f0416f"/></svg>Propertis</div>
</div>
<div class="stat small tenants">
  <div class="value">8</div>
  <div class="label"><svg width="13" height="13" viewBox="0 0 13 13" aria-hidden="true"><circle cx="6.5" cy="6.5" r="6.5" fill="#fff"/><circle cx="6.5" cy="5" r="2.2" fill="#1f5fc0"/><path d="M2.8 10.5 a3.7 3 0 0 1 7.4 0Z" fill="#1f5fc0"/></svg>Tenants</div>
</div>

<div class="stat area total">
  <div class="value">422,000.00 Sq.ft.</div>
  <div class="label"><svg width="14" height="14" viewBox="0 0 14 14" aria-hidden="true"><circle cx="7" cy="7" r="6.2" fill="none" stroke="#fff" stroke-width="1.5"/><circle cx="7" cy="7" r="3.5" fill="none" stroke="#fff" stroke-width="1.3"/><path d="M7 7 L12 2" stroke="#fff" stroke-width="1.5"/></svg>Total Properties Area</div>
</div>
<div class="stat area rented">
  <div class="value">233,500.00 sq.ft</div>
  <div class="label"><svg width="14" height="14" viewBox="0 0 14 14" aria-hidden="true"><circle cx="7" cy="7" r="6.2" fill="none" stroke="#fff" stroke-width="1.5"/><circle cx="7" cy="7" r="3.5" fill="none" stroke="#fff" stroke-width="1.3"/><path d="M7 7 L12 2" stroke="#fff" stroke-width="1.5"/></svg>Rented Area</div>
</div>
<div class="stat area vacant">
  <div class="value">188,500.00 sq.ft</div>
  <div class="label"><svg width="14" height="14" viewBox="0 0 14 14" aria-hidden="true"><circle cx="7" cy="7" r="6.2" fill="none" stroke="#fff" stroke-width="1.5"/><circle cx="7" cy="7" r="3.5" fill="none" stroke="#fff" stroke-width="1.3"/><path d="M7 7 L12 2" stroke="#fff" stroke-width="1.5"/></svg>Vacancies Area</div>
</div>

<section class="chart-panel">
  <svg width="793" height="460" viewBox="0 0 793 460" font-family="Roboto, Arial, sans-serif" font-size="10" fill="#333">
    <g class="columns">
      <rect x="66" y="20" width="101" height="397" fill="#f5e5ec"/>
      <rect x="167" y="20" width="101" height="397" fill="#c5dff8"/>
      <rect x="268" y="20" width="101" height="397" fill="#f5e5ec"/>
      <rect x="369" y="20" width="101" height="397" fill="#c5dff8"/>
      <rect x="470" y="20" width="101" height="397" fill="#f5e5ec"/>
      <rect x="571" y="20" width="101" height="397" fill="#c5dff8"/>
      <rect x="672" y="20" width="101" height="397" fill="#f5e5ec"/>
    </g>
    <g class="grid" stroke="#8d8d8d" stroke-width="0.7">
      <line x1="66" y1="52" x2="779" y2="52"/>
      <line x1="66" y1="124.5" x2="779" y2="124.5"/>
      <line x1="66" y1="197" x2="779" y2="197"/>
      <line x1="66" y1="271" x2="779" y2="271"/>
      <line x1="66" y1="344" x2="779" y2="344"/>
      <line x1="66" y1="417" x2="779" y2="417"/>
      <line x1="66" y1="20" x2="66" y2="417"/>
    </g>
    <path d="M401 417 V131.5 a6.5 6.5 0 0 1 6.5 -6.5 H416.5 a6.5 6.5 0 0 1 6.5 6.5 V417 Z" fill="#77b4f0"/>
    <g class="y-labels" text-anchor="end">
      <text x="57" y="49">1.25</text>
      <text x="57" y="120">1.00</text>
      <text x="57" y="193">0.75</text>
      <text x="57" y="266">0.50</text>
      <text x="57" y="341">0.25</text>
      <text x="43" y="413">0</text>
    </g>
    <text x="17" y="219" text-anchor="middle" transform="rotate(-90 17 219)">Number</text>
    <g class="x-labels" text-anchor="middle">
      <text x="117" y="441">27/12/2020</text>
      <text x="218" y="441">28/12/2020</text>
      <text x="319" y="441">29/12/2020</text>
      <text x="420" y="441">30/12/2020</text>
      <text x="521" y="441">31/12/2020</text>
      <text x="622" y="441">01/01/2020</text>
      <text x="723" y="441">02/01/2020</text>
    </g>
  </svg>
</section>

<div class="legend">
  <div class="legend-item" style="left:41px;top:13px"><span class="dot" style="background:#6ab0f5"></span>Scheduled Maintenance</div>
  <div class="legend-item" style="left:243px;top:12px"><span class="dot" style="background:#7ee07a"></span>Completed Scheduled Maintenance</div>
  <div class="legend-item" style="left:526px;top:13px"><span class="dot" style="background:#f0a06a"></span>Future Scheduled Maintenance</div>
  <div class="legend-item" style="left:795px;top:13px"><span class="dot" style="background:#3a3d4a"></span>Scheduled Work Orders</div>
  <div class="legend-item" style="left:41px;top:41px"><span class="dot" style="background:#8a86d8"></span>Completed Work Orders</div>
  <div class="legend-item" style="left:244px;top:43px"><span class="dot" style="background:#f04a78"></span>Property Inspections in Progress</div>
  <div class="legend-item" style="left:526px;top:43px"><span class="dot" style="background:#e6d650"></span>Completed Property Inspections</div>
</div>

<nav class="sidebar">
  <div class="nav-item active"><svg viewBox="0 0 16 16"><path d="M8 1 L16 8 H13.5 V15 H10 V10.5 H6 V15 H2.5 V8 H0 Z" fill="#fff"/></svg>Dashboard</div>
  <div class="nav-item"><svg viewBox="0 0 16 16"><circle cx="5" cy="4.5" r="3" fill="#fff"/><circle cx="11.5" cy="4.5" r="2.6" fill="#fff"/><path d="M0 14 a5 5 0 0 1 10 0Z M9 14 a4 4 0 0 1 7 -1 V14Z" fill="#fff"/></svg>Customers</div>
  <div class="nav-item"><svg viewBox="0 0 16 16"><path d="M8 1 L16 8 H13.5 V15 H2.5 V8 H0 Z" fill="#fff"/><rect x="6.5" y="10" width="3" height="5" fill="#1638c8"/></svg>Properties</div>
  <div class="nav-item"><svg viewBox="0 0 16 16"><circle cx="8" cy="8" r="7.5" fill="#fff"/><circle cx="8" cy="6.3" r="2.5" fill="#1638c8"/><path d="M3.8 12.5 a4.2 3.4 0 0 1 8.4 0Z" fill="#1638c8"/></svg>Tenants</div>
  <div class="nav-item"><svg viewBox="0 0 16 16"><circle cx="8" cy="6" r="5" fill="none" stroke="#fff" stroke-width="1.8"/><circle cx="8" cy="5.5" r="2" fill="#fff"/><rect x="3" y="12" width="10" height="3.5" rx="1" fill="#fff"/></svg>Contacts</div>
  <div class="nav-item"><svg viewBox="0 0 16 16"><circle cx="5.5" cy="6" r="4" fill="none" stroke="#fff" stroke-width="2.4" stroke-dasharray="2 1.2"/><circle cx="12" cy="12" r="2.8" fill="none" stroke="#fff" stroke-width="2" stroke-dasharray="1.6 1"/><circle cx="12.5" cy="3.5" r="2" fill="none" stroke="#fff" stroke-width="1.6"/></svg>Contractors</div>
  <div class="nav-item"><svg viewBox="0 0 16 16"><circle cx="8" cy="4" r="2.3" fill="#fff"/><circle cx="3" cy="6" r="2" fill="#fff"/><circle cx="13" cy="6" r="2" fill="#fff"/><path d="M4 13 a4 4 0 0 1 8 0Z M0 13 a3 3 0 0 1 5 -2.5 L4 13Z M16 13 a3 3 0 0 0 -5 -2.5 L12 13Z" fill="#fff"/></svg>Employees</div>
  <div class="nav-item"><svg viewBox="0 0 16 16"><rect x="1" y="2" width="14" height="12" rx="1" fill="none" stroke="#fff" stroke-width="1.6"/><path d="M4 6 H12 M4 8.5 H12 M4 11 H9" stroke="#fff" stroke-width="1.4"/></svg>Prevents,Maintenance</div>
  <div class="nav-item"><svg viewBox="0 0 16 16"><circle cx="6.5" cy="6.5" r="4.3" fill="none" stroke="#fff" stroke-width="2.6" stroke-dasharray="2 1.3"/><circle cx="12" cy="12" r="2.6" fill="none" stroke="#fff" stroke-width="2" stroke-dasharray="1.5 1"/></svg>Work Orders</div>
  <div class="nav-item"><svg viewBox="0 0 16 16"><path d="M3 5 H13 L12 15 H4 Z" fill="#fff"/><path d="M5.5 5 V3.5 a2.5 2.5 0 0 1 5 0 V5" fill="none" stroke="#fff" stroke-width="1.4"/><circle cx="8" cy="10" r="1.8" fill="#1638c8"/></svg>Purchase Orders</div>
  <div class="nav-item"><svg viewBox="0 0 16 16"><path d="M2 1 H9 V15 H2 Z" fill="none" stroke="#fff" stroke-width="1.6"/><circle cx="10" cy="9" r="3" fill="none" stroke="#fff" stroke-width="1.6"/><path d="M12 11 L15 14.5" stroke="#fff" stroke-width="1.8"/></svg>Proerties Inspections</div>
  <div class="nav-item"><svg viewBox="0 0 16 16"><rect x="1" y="8" width="2.5" height="6" fill="#fff"/><rect x="5" y="3" width="2.5" height="11" fill="#fff"/><rect x="9" y="6" width="2.5" height="8" fill="#fff"/><rect x="13" y="10" width="2.5" height="4" fill="#fff"/><rect x="0" y="14.5" width="16" height="1.5" fill="#fff"/></svg>Energy Management</div>
  <div class="nav-item"><svg viewBox="0 0 16 16"><path d="M8 1 L15.5 15 H0.5 Z" fill="#fff"/><rect x="7.2" y="6" width="1.6" height="5" fill="#1638c8"/><circle cx="8" cy="12.7" r="0.9" fill="#1638c8"/></svg>Risk Mangement</div>
  <div class="nav-item"><svg viewBox="0 0 16 16"><g fill="#fff"><rect x="0" y="2" width="2.5" height="2.5"/><rect x="4" y="2" width="12" height="2.5"/><rect x="0" y="6.8" width="2.5" height="2.5"/><rect x="4" y="6.8" width="12" height="2.5"/><rect x="0" y="11.5" width="2.5" height="2.5"/><rect x="4" y="11.5" width="12" height="2.5"/></g></svg>Project Management</div>
  <div class="nav-item"><svg viewBox="0 0 16 16"><circle cx="10" cy="6" r="5" fill="none" stroke="#fff" stroke-width="1.5"/><circle cx="6.5" cy="9.5" r="5.5" fill="#fff"/><text x="6.5" y="12.5" font-size="8" text-anchor="middle" fill="#1638c8" font-family="Roboto, Arial, sans-serif">$</text></svg>Finacial-Budgeting</div>
  <div class="nav-item"><svg viewBox="0 0 16 16"><path d="M1 2 H15 V11 H6 L2 14.5 V11 H1 Z" fill="#fff"/><circle cx="5" cy="6.5" r="1" fill="#1638c8"/><circle cx="8" cy="6.5" r="1" fill="#1638c8"/><circle cx="11" cy="6.5" r="1" fill="#1638c8"/></svg>Tenants Requests</div>
  <div class="nav-item"><svg viewBox="0 0 16 16"><rect x="3" y="1" width="11" height="14" rx="1" fill="#fff"/><path d="M6 5 H11 M6 8 H11 M6 11 H9" stroke="#1638c8" stroke-width="1.3"/><rect x="1" y="3" width="3" height="2" fill="#fff"/><rect x="1" y="10" width="3" height="2" fill="#fff"/></svg>Repors</div>
  <div class="nav-item"><svg viewBox="0 0 16 16"><path d="M1 11 L5 6 L8 9 L14 3" fill="none" stroke="#fff" stroke-width="1.8"/><path d="M0 15 L5 9 L8 12 L16 6 V15 Z" fill="#fff"/></svg>Visual Reports</div>
  <div class="nav-item"><svg viewBox="0 0 16 16"><path d="M3 2 H8 L9.5 3.5 H15 V12 H3 Z" fill="#fff"/><path d="M1 5 V14.5 H13" fill="none" stroke="#fff" stroke-width="1.6"/></svg>Files</div>
  <div class="nav-item"><svg viewBox="0 0 16 16"><path d="M3 1 H10 L13.5 4.5 V15 H3 Z" fill="#fff"/><path d="M5.5 8 H11 M5.5 10.5 H11 M5.5 13 H9" stroke="#1638c8" stroke-width="1.2"/></svg>pages</div>
  <div class="nav-item"><svg viewBox="0 0 16 16"><circle cx="6" cy="10" r="4" fill="none" stroke="#fff" stroke-width="2.6" stroke-dasharray="2 1.2"/><circle cx="12.5" cy="3.8" r="2.3" fill="none" stroke="#fff" stroke-width="1.8" stroke-dasharray="1.4 0.9"/></svg>Configurations</div>
  <div class="nav-item"><svg viewBox="0 0 16 16"><path d="M2 2 L14 14 M14 2 L2 14" stroke="#fff" stroke-width="2.2"/><circle cx="3" cy="3" r="2.3" fill="#fff"/><circle cx="13" cy="13" r="2.3" fill="#fff"/></svg>Settings</div>
</nav>

</body>
</html>
```